Business Card Design for Training Business

Clear Path Coaching is a new business that delivers training and other services with a focus on topics related to mental health and wellbeing, for example, Wellmind Response Course, Resilience etc. We have a strong focus on evidence-based psychology and neuroscience. I have a logo which I will upload with the brief, so please consider colours that work well with the logo.
Target Market(s)
Adults, workplaces (particularly government and not-for-profits)
Industry/Entity Type
Business
Contact Information for Business Card
Head Strong TrainingSamantha SellwoodDirector0438 770 850sam@headstrongtraining.com.auwww.headstrongtraining.com.au

```html
<!DOCTYPE html>
<html lang="en">
<head>
<meta charset="utf-8">
<title>Clear Path Coaching – Business Card</title>
<link href="https://fonts.googleapis.com/css2?family=Questrial&display=swap" rel="stylesheet">
<style>
  :root {
    --teal: #22b6bb;
    --teal-deep: #1fb0b5;
    --paper: #f7f7f7;
    --ink: #4a4a4a;
    --mark-grey: #7d7d7d;
    --stage: #333333;
    --white: #ffffff;
  }
  * { margin: 0; padding: 0; box-sizing: border-box; }
  html, body {
    width: 1200px;
    height: 750px;
    overflow: hidden;
    background: var(--stage);
    font-family: "Questrial", "Century Gothic", sans-serif;
  }
  .card {
    position: absolute;
    left: 371px;
    width: 461px;
    height: 262px;
  }
  .card--front { top: 106px; background: var(--paper); }
  .card--back { top: 387px; background: var(--teal-deep); }

  .brand {
    position: absolute;
    left: 590px;
    top: 126px;
    width: 240px;
    text-align: center;
    color: var(--mark-grey);
    font-size: 15px;
    letter-spacing: 2.5px;
    line-height: 1.35;
    text-transform: uppercase;
  }
  .brand__dot {
    display: block;
    width: 62px;
    height: 62px;
    margin: 0 auto 14px;
    border: 1.5px solid var(--teal);
    border-radius: 50%;
  }

  .accent-bar {
    position: absolute;
    left: 0;
    top: 145px;
    width: 8px;
    height: 34px;
    background: var(--teal);
  }
  .person {
    position: absolute;
    left: 23px;
    top: 143px;
  }
  .person__name {
    color: var(--teal);
    font-size: 20px;
    line-height: 1.2;
  }
  .person__role {
    color: var(--ink);
    font-size: 14px;
    line-height: 1.2;
  }
  .contacts {
    position: absolute;
    left: 25px;
    top: 193px;
    list-style: none;
  }
  .contacts__item {
    display: flex;
    align-items: center;
    height: 17.5px;
    color: var(--ink);
    font-size: 12.5px;
  }
  .contacts__icon {
    width: 12px;
    height: 12px;
    margin-right: 8px;
    flex: none;
  }

  .back__brand {
    position: absolute;
    left: 175px;
    top: 77px;
    width: 110px;
    height: 110px;
    border: 1.5px solid var(--white);
    border-radius: 50%;
  }
  .back__url {
    position: absolute;
    left: 0;
    top: 227px;
    width: 100%;
    text-align: center;
    color: var(--white);
    font-size: 12.5px;
  }
</style>
</head>
<body>
  <section class="card card--front">
    <div class="brand" style="left:219px;top:20px;width:240px;">
      <span class="brand__dot"></span>
      Clear Path<br>Coaching
    </div>

    <span class="accent-bar"></span>
    <div class="person">
      <p class="person__name">Rebecca Tanfield</p>
      <p class="person__role">Director</p>
    </div>

    <ul class="contacts">
      <li class="contacts__item">
        <svg class="contacts__icon" viewBox="0 0 12 12" aria-hidden="true">
          <path d="M2.4 1 L4.2 1 L4.9 3.4 L3.8 4.4 C4.5 5.9 5.9 7.4 7.6 8.2 L8.6 7.1 L11 7.8 L11 9.6 C11 10.4 10.4 11 9.6 11 C5 10.7 1.3 7 1 2.4 C1 1.6 1.6 1 2.4 1 Z" fill="var(--teal)"/>
        </svg>
        0491 362 517
      </li>
      <li class="contacts__item">
        <svg class="contacts__icon" viewBox="0 0 12 12" aria-hidden="true">
          <rect x="0.5" y="2.5" width="11" height="7.5" fill="var(--teal)"/>
          <path d="M0.8 2.9 L6 6.6 L11.2 2.9" fill="none" stroke="var(--paper)" stroke-width="0.9"/>
        </svg>
        bec@clearpathcoaching.example.au
      </li>
      <li class="contacts__item">
        <svg class="contacts__icon" viewBox="0 0 12 12" aria-hidden="true">
          <circle cx="6" cy="6" r="5.5" fill="var(--teal)"/>
          <path d="M3 3.5 C4.5 4 4 6 5.5 6.5 C6.5 7 6 9 7 10 M8 2 C7.5 3.5 9 4 10 4.5" fill="none" stroke="var(--paper)" stroke-width="0.9"/>
        </svg>
        www.clearpathcoaching.example.au
      </li>
    </ul>
  </section>

  <section class="card card--back">
    <span class="back__brand" aria-hidden="true"></span>
    <p class="back__url">www.clearpathcoaching.example.au</p>
  </section>
</body>
</html>
```